Small legal and financial translation company needs Squarespace website, brochure and logo

Hello,
We are Lumarin Services (www.lumarinservices-example.com), a boutique legal and financial translation company. We offer our services mainly to Spanish customers. Our primary line of business is the translation of financial statements, but we translate a wide variety legal and financial texts.
The project we are offering comprises three parts: a redo of the current website, an informational brochure for potential customer and a logo design. These three parts should provide a consistent image. We would develop content soon.
We are looking for a website that would look like a typical law firm website, nothing too fancy. Right now, it is in English, Spanish and French, although the new site need only be in English and Spanish. There must be good toggling between the English and Spanish versions. There would be no need for tie-ins to social media and it would not contain a blog. Basically, a static site. We aren't interesting in driving traffic to the site or SEO, as we will contact nearly all potential customers beforehand. The website must be built in Squarespace to enable a smooth transition. The content would be similar to the current page, we'll be working on the exact content, but a rough draft is attached.
The brochure will be some three pages and would introduce the company to potential customers, using similar images as the website and the logo to be designed.
The only specifications for the logo is, as the website and brochure, it convey a sense of security and trust.
Feel free to ask with any questions as this is the first time we have used this platform.
Thank you!
Updates

I've added a more or less final version for the text in the brochure and updated the brief. Added Wednesday, June 10, 2015

Target Market(s)

Spanish law firms, auditors, accountants, banks, investment firms

Industry/Entity Type

Finance

Logo Text

Lumarin Services

Number of Pages Required

5+ page

Font styles to use
Serif

Requirements
Must have
• The website must be built in Squarespace and have a good option to toggle between English and Spanish versions.
• Brochure must be in both English and Spanish, I'm attaching a rough draft of the information that it will probably have. This should give an idea about what to include and the spacing. I will update it to include the final information.
Nice to have
• Would be nice to have some quality finance- and legal-related images
Should not have
• Vibrant colours

```html
<!DOCTYPE html>
<html lang="en">
<head>
<meta charset="utf-8">
<title>Lumarin Services – Pricing Brochure Spread</title>
<link rel="stylesheet" href="https://fonts.googleapis.com/css2?family=Linden+Hill&family=Playfair+Display:ital,wght@1,700&display=swap">
<style>
  :root {
    --backdrop: #e9e7e3;
    --page-dark: #1c1c1e;
    --page-mid: #2e2e31;
    --page-light: #3d3d40;
    --rule: #f2f2f2;
    --text-light: #eeeeee;
    --accent-teal: #5aa7b6;
    --band-slate: #5d7378;
    --photo-dark: #3a3a3a;
    --photo-light: #c9c9c9;
    --still-dark: #4a4039;
    --still-light: #b9aca0;
  }
  * { margin: 0; padding: 0; box-sizing: border-box; }
  html, body {
    width: 1200px; height: 537px; overflow: hidden;
    background: var(--backdrop);
  }
  .spread {
    position: absolute; left: 55px; top: 75px;
    width: 1105px; height: 390px;
    display: flex;
    box-shadow: 0 2px 10px rgba(0,0,0,0.25);
  }
  .page { position: relative; height: 100%; }
  .page--left { width: 553px; background: var(--photo-dark); }
  .page--right {
    width: 552px;
    background: linear-gradient(100deg, var(--page-dark) 0%, var(--page-light) 30%, var(--page-mid) 55%, var(--page-dark) 100%);
    border-left: 1px solid #111;
  }
  .street-photo {
    position: absolute; left: 0; top: 0; width: 100%; height: 380px;
    background:
      linear-gradient(180deg, rgba(255,255,255,0) 0%, rgba(0,0,0,0.35) 100%),
      linear-gradient(90deg, #505050 0%, #8a8a8a 22%, var(--photo-light) 45%, #9a9a9a 58%, #3c3c3c 75%, #262626 100%);
  }
  .band-teal {
    position: absolute; left: 0; bottom: 0; width: 100%; height: 10px;
    background: linear-gradient(90deg, #6fb3c2, var(--accent-teal), #7fbccb);
  }
  .band-slate {
    position: absolute; left: 0; bottom: 0; width: 100%; height: 10px;
    background: var(--band-slate);
  }
  .brand {
    position: absolute; left: 50px; top: 20px;
    font-family: "Linden Hill", serif;
    font-size: 20px; color: var(--accent-teal);
    letter-spacing: 0.5px;
  }
  .section-title {
    position: absolute; right: 28px;
    font-family: "Playfair Display", serif;
    font-style: italic; font-weight: 700;
    font-size: 20px; color: var(--text-light);
  }
  .section-rule {
    position: absolute; left: 252px; right: 24px; height: 2px;
    background: var(--rule);
  }
  .section-copy {
    position: absolute; left: 265px; width: 264px;
    font-family: "Linden Hill", serif;
    font-size: 11.6px; line-height: 14.3px;
    color: var(--text-light);
  }
  .pricing-title { top: 24px; }
  .pricing-rule { top: 49px; }
  .pricing-copy { top: 63px; }
  .precios-title { top: 197px; }
  .precios-rule { top: 223px; }
  .precios-copy { top: 239px; width: 270px; }
  .still {
    position: absolute; left: 50px; width: 115px;
    background: linear-gradient(135deg, var(--still-light) 0%, #8d8078 50%, var(--still-dark) 100%);
  }
  .still--glasses { top: 216px; height: 76px; }
  .still--pen { top: 300px; height: 68px; }
</style>
</head>
<body>
  <main class="spread">
    <section class="page page--left">
      <div class="street-photo" role="img" aria-label="Black and white photograph of a steep city street lined with old stone buildings, a lone pedestrian crossing"></div>
      <div class="band-teal"></div>
    </section>
    <section class="page page--right">
      <div class="brand">Lumarin Services</div>

      <h2 class="section-title pricing-title">Pricing</h2>
      <div class="section-rule pricing-rule"></div>
      <p class="section-copy pricing-copy">Our prices take into account a wide variety of factors based on each individual job to be carried out. Urgency, formatting, past experience, technical complexity and many other factors go into preparing a quote tailored to customers' needs. We are always happy to discuss pricing with our customers, although a basic starting point for any job stands around EUR 0.085/word.</p>

      <div class="still still--glasses" role="img" aria-label="Sepia photograph of reading glasses resting on documents"></div>
      <div class="still still--pen" role="img" aria-label="Sepia photograph of a fountain pen on paperwork"></div>

      <h2 class="section-title precios-title" lang="es">Precios</h2>
      <div class="section-rule precios-rule"></div>
      <p class="section-copy precios-copy" lang="es">Nuestros precios tienen en cuenta una amplia variedad de factores basados en cada trabajo individual a realizar. Urgencia, el formato, la experiencia pasada, la complejidad técnica y muchos otros factores entran en la preparación de un presupuesto adaptado a las necesidades de los clientes. Siempre estamos dispuestos a discutir el precio con nuestros clientes, a pesar de un punto de partida básico para cualquier trabajo representa alrededor 0.085 euros / palabra.</p>

      <div class="band-slate"></div>
    </section>
  </main>
</body>
</html>
```